Car wash line needed for the pylon inscription

We need a design template / print template for our advertising pylon so that the Korvane plates can be printed. The area to be printed is approx. 1.5m wide and approx. 2.70m high. We operate a car wash about 30m long. The washing rollers are equipped with scratch-free Velmo Tex foam material. Before the vehicle is put into the car wash it gets a manual high pressure pre-wash. There are four different washing programs: basic laundry € 7.50 (wheel cleaning, intensive washing, gloss drying comfort care € 10.50 (like base + active foam) special care € 13.00 (like comfort + glossy sealing with lotus wax) premium care € 15.50 (like special care + Underbody wash) The pylon is right on the driveway on a busy road, we want to achieve maximum attention with the pylons. It should not be too much content because the vehicles drive past it, due to an immediate gyro, the speed is however at about 40Km / h. Opening hours Mon-Fri. 08: 00-19: 00 Sat 07: 00-19: 00 The Korvane plates are red. The enclosed files show our pylon with a little appealing design proposal our advertising agency and the real local places. For the opinion you can see on the following link a youtube video with a comparable car wash like ours, the washing process is well illustrated there. https://www.clipvault-demo.net/watch?v=Qk7rTzP2mLw Furthermore, we have a bonus card system who has washed our car 10 times gets the 11 laundry for free. From foam additives we use active foam from the comfort care and from the special care gets the vehicle lotus wax, which has the effect that the paint is sealed and keeps the shine longer. We need a design template / print template for our advertising pylon so that the Korvane plates can be printed. The area to be printed is approx. 1.5m wide and approx. 2.70m high. We operate a car wash about 30m long. The washing rollers are equipped with scratch-free Velmo Tex foam material. Before the vehicle is put into the car wash it gets a manual high pressure pre-wash. There are four different washing programs: basic laundry € 7.50 (wheel cleaning, intensive washing, gloss drying comfort care € 10.50 (like base + active foam) special care € 13.00 (like comfort + glossy sealing with lotus wax) premium care € 15.50 (like special care + Underbody wash) The pylon is right on the driveway on a busy road, we want to achieve maximum attention with the pylons. It should not be too much content because the vehicles drive past it, due to an immediate gyro, the speed is however at about 40Km / h. Opening hours Mon-Fri. 08: 00-19: 00 Sat 07: 00-19: 00 The Korvane plates are red. The enclosed files show our pylon with a little appealing design proposal our advertising agency and the real local places. For the opinion you can see on the following link a youtube video with a comparable car wash like ours, the washing process is well illustrated there. https://www.clipvault-demo.net/watch?v=Qk7rTzP2mLw Furthermore, we have a bonus card system who has washed our car 10 times gets the 11 laundry for free. From foam additives we use active foam from the comfort care and from the special care gets the vehicle lotus wax, which has the effect that the paint is sealed and keeps the shine longer. We need a design template / print template for our advertising pylon so that the Korvane plates can be printed. The area to be printed is approx. 1.5m wide and approx. 2.70m high. We operate a car wash about 30m long. The washing rollers are equipped with scratch-free Velmo Tex foam material. Before the vehicle is put into the car wash it gets a manual high pressure pre-wash. There are four different washing programs: basic laundry € 7.50 (wheel cleaning, intensive washing, gloss drying comfort care € 10.50 (like base + active foam) special care € 13.00 (like comfort + glossy sealing with lotus wax) premium care € 15.50 (like special care + Underbody wash) The pylon is right on the driveway on a busy road, we want to achieve maximum attention with the pylons. It should not be too much content because the vehicles drive past it, due to an immediate gyro, the speed is however at about 40Km / h. Opening hours Mon-Fri. 08: 00-19: 00 Sat 07: 00-19: 00 The Korvane plates are red. The enclosed files show our pylon with a little appealing design proposal our advertising agency and the real local places. For the opinion you can see on the following link a youtube video with a comparable car wash like ours, the washing process is well illustrated there. https://www.clipvault-demo.net/watch?v=Qk7rTzP2mLw Furthermore, we have a bonus card system who has washed our car 10 times gets the 11 laundry for free. From foam additives we use active foam from the comfort care and from the special care gets the vehicle lotus wax, which has the effect that the paint is sealed and keeps the shine longer. We need a design template / print template for our advertising pylon so that the Korvane plates can be printed. The area to be printed is approx. 1.5m wide and approx. 2.70m high. We operate a car wash about 30m long. The washing rollers are equipped with scratch-free Velmo Tex foam material. Before the vehicle is put into the car wash it gets a manual high pressure pre-wash. There are four different washing programs: basic laundry € 7.50 (wheel cleaning, intensive washing, gloss drying comfort care € 10.50 (like base + active foam) special care € 13.00 (like comfort + glossy sealing with lotus wax) premium care € 15.50 (like special care + Underbody wash) The pylon is right on the driveway on a busy road, we want to achieve maximum attention with the pylons. It should not be too much content because the vehicles drive past it, due to an immediate gyro, the speed is however at about 40Km / h. Opening hours Mon-Fri. 08: 00-19: 00 Sat 07: 00-19: 00 The Korvane plates are red. The enclosed files show our pylon with a little appealing design proposal our advertising agency and the real local places. For the opinion you can see on the following link a youtube video with a comparable car wash like ours, the washing process is well illustrated there. https://www.clipvault-demo.net/watch?v=Qk7rTzP2mLw Furthermore, we have a bonus card system who has washed our car 10 times gets the 11 laundry for free. From foam additives we use active foam from the comfort care and from the special care gets the vehicle lotus wax, which has the effect that the paint is sealed and keeps the shine longer. We need a design template / print template for our advertising pylon so that the Korvane plates can be printed. The area to be printed is approx. 1.5m wide and approx. 2.70m high. We operate a car wash about 30m long. The washing rollers are equipped with scratch-free Velmo Tex foam material. Before the vehicle is put into the car wash it gets a manual high pressure pre-wash. There are four different washing programs: basic laundry € 7.50 (wheel cleaning, intensive washing, gloss drying comfort care € 10.50 (like base + active foam) special care € 13.00 (like comfort + glossy sealing with lotus wax) premium care € 15.50 (like special care + Underbody wash) The pylon is right on the driveway on a busy road, we want to achieve maximum attention with the pylons. It should not be too much content because the vehicles drive past it, due to an immediate gyro, the speed is however at about 40Km / h. Opening hours Mon-Fri. 08: 00-19: 00 Sat 07: 00-19: 00 The Korvane plates are red. The enclosed files show our pylon with a little appealing design proposal our advertising agency and the real local places. For the opinion you can see on the following link a youtube video with a comparable car wash like ours, the washing process is well illustrated there. https://www.clipvault-demo.net/watch?v=Qk7rTzP2mLw Furthermore, we have a bonus card system who has washed our car 10 times gets the 11 laundry for free. From foam additives we use active foam from the comfort care and from the special care gets the vehicle lotus wax, which has the effect that the paint is sealed and keeps the shine longer. We need a design template / print template for our advertising pylon so that the Korvane plates can be printed. The area to be printed is approx. 1.5m wide and approx. 2.70m high. We operate a car wash about 30m long. The washing rollers are equipped with scratch-free Velmo Tex foam material. Before the vehicle is put into the car wash it gets a manual high pressure pre-wash. There are four different washing programs: basic laundry € 7.50 (wheel cleaning, intensive washing, gloss drying comfort care € 10.50 (like base + active foam) special care € 13.00 (like comfort + glossy sealing with lotus wax) premium care € 15.50 (like special care + Underbody wash) The pylon is right on the driveway on a busy road, we want to achieve maximum attention with the pylons. It should not be too much content because the vehicles drive past it, due to an immediate gyro, the speed is however at about 40Km / h. Opening hours Mon-Fri. 08: 00-19: 00 Sat 07: 00-19: 00 The Korvane plates are red. The enclosed files show our pylon with a little appealing design proposal our advertising agency and the real local places. For the opinion you can see on the following link a youtube video with a comparable car wash like ours, the washing process is well illustrated there. https://www.clipvault-demo.net/watch?v=Qk7rTzP2mLw Furthermore, we have a bonus card system who has washed our car 10 times gets the 11 laundry for free. From foam additives we use active foam from the comfort care and from the special care gets the vehicle lotus wax, which has the effect that the paint is sealed and keeps the shine longer. We need a design template / print template for our advertising pylon so that the Korvane plates can be printed. The area to be printed is approx. 1.5m wide and approx. 2.70m high. We operate a car wash about 30m long. The washing rollers are equipped with scratch-free Velmo Tex foam material. Before the vehicle is put into the car wash it gets a manual high pressure pre-wash. There are four different washing programs: basic laundry € 7.50 (wheel cleaning, intensive washing, gloss drying comfort care € 10.50 (like base + active foam) special care € 13.00 (like comfort + glossy sealing with lotus wax) premium care € 15.50 (like special care + Underbody wash) The pylon is right on the driveway on a busy road, we want to achieve maximum attention with the pylons. It should not be too much content because the vehicles drive past it, due to an immediate gyro, the speed is however at about 40Km / h. Opening hours Mon-Fri. 08: 00-19: 00 Sat 07: 00-19: 00 The Korvane plates are red. The enclosed files show our pylon with a little appealing design proposal our advertising agency and the real local places. For the opinion you can see on the following link a youtube video with a comparable car wash like ours, the washing process is well illustrated there. https://www.clipvault-demo.net/watch?v=Qk7rTzP2mLw Furthermore, we have a bonus card system who has washed our car 10 times gets the 11 laundry for free. From foam additives we use active foam from the comfort care and from the special care gets the vehicle lotus wax, which has the effect that the paint is sealed and keeps the shine longer. We need a design template / print template for our advertising pylon so that the Korvane plates can be printed. The area to be printed is approx. 1.5m wide and approx. 2.70m high. We operate a car wash about 30m long. The washing rollers are equipped with scratch-free Velmo Tex foam material. Before the vehicle is put into the car wash it gets a manual high pressure pre-wash. There are four different washing programs: basic laundry € 7.50 (wheel cleaning, intensive washing, gloss drying comfort care € 10.50 (like base + active foam) special care € 13.00 (like comfort + glossy sealing with lotus wax) premium care € 15.50 (like special care + Underbody wash) The pylon is right on the driveway on a busy road, we want to achieve maximum attention with the pylons. It should not be too much content because the vehicles drive past it, due to an immediate gyro, the speed is however at about 40Km / h. Opening hours Mon-Fri. 08: 00-19: 00 Sat 07: 00-19: 00 The Korvane plates are red. The enclosed files show our pylon with a little appealing design proposal our advertising agency and the real local places. For the opinion you can see on the following link a youtube video with a comparable car wash like ours, the washing process is well illustrated there. https://www.clipvault-demo.net/watch?v=Qk7rTzP2mLw Furthermore, we have a bonus card system who has washed our car 10 times gets the 11 laundry for free. From foam additives we use active foam from the comfort care and from the special care gets the vehicle lotus wax, which has the effect that the paint is sealed and keeps the shine longer. We need a design template / print template for our advertising pylon so that the Korvane plates can be printed. The area to be printed is approx. 1.5m wide and approx. 2.70m high. We operate a car wash about 30m long. The washing rollers are equipped with scratch-free Velmo Tex foam material. Before the vehicle is put into the car wash it gets a manual high pressure pre-wash. There are four different washing programs: basic laundry € 7.50 (wheel cleaning, intensive washing, gloss drying comfort care € 10.50 (like base + active foam) special care € 13.00 (like comfort + glossy sealing with lotus wax) premium care € 15.50 (like special care + Underbody wash) The pylon is right on the driveway on a busy road, we want to achieve maximum attention with the pylons. It should not be too much content because the vehicles drive past it, due to an immediate gyro, the speed is however at about 40Km / h. Opening hours Mon-Fri. 08: 00-19: 00 Sat 07: 00-19: 00 The Korvane plates are red. The enclosed files show our pylon with a little appealing design proposal our advertising agency and the real local places. For the opinion you can see on the following link a youtube video with a comparable car wash like ours, the washing process is well illustrated there. https://www.clipvault-demo.net/watch?v=Qk7rTzP2mLw Furthermore, we have a bonus card system who has washed our car 10 times gets the 11 laundry for free. From foam additives we use active foam from the comfort care and from the special care gets the vehicle lotus wax, which has the effect that the paint is sealed and keeps the shine longer.

Target Market(s)

germany

Colors

Designer to choose colors to be used in the design.

Requirements
Must have
• Print template for the print job in the accepted formats. Of course, the design must be in German
Nice to have
• Colors that attract attention, but are still serious. The content must be perceived when passing by and the customers must be aware of the car wash.
Should not have
• Kitschiges Design Too much content which takes longer to be read.

```html
<!DOCTYPE html>
<html lang="de">
<head>
<meta charset="utf-8">
<title>Autowäsche – Pylon</title>
<link rel="stylesheet" href="https://fonts.googleapis.com/css2?family=Anton&family=Roboto:ital,wght@0,400;0,700;0,900;1,700;1,900&display=swap">
<style>
  :root {
    --sky: #79d6e8;
    --sky-deep: #2cc0da;
    --navy: #0b2a63;
    --navy-deep: #071c4a;
    --ocean: #0a8fc4;
    --signal-red: #ee1c25;
    --banner-edge: #163a8a;
    --white: #ffffff;
    --label-grey: #e6e9f0;
    --gold: #ffe21a;
    --teal: #3cc6d0;
    --page: #ffffff;
  }
  html, body {
    margin: 0;
    width: 960px;
    height: 1200px;
    overflow: hidden;
    background: var(--page);
  }
  .stage {
    width: 960px;
    height: 1200px;
    display: flex;
    align-items: center;
    justify-content: center;
  }
  .pylon-face { display: block; }
  .title { font-family: "Anton", sans-serif; }
  .bullet-text, .promo-text, .extra-line, .hours-line {
    font-family: "Roboto", sans-serif;
    font-style: italic;
  }
  .bullet-text { font-weight: 700; font-size: 42px; fill: var(--white); }
  .price-euro, .price-value {
    font-family: "Roboto", sans-serif;
    font-weight: 900;
    fill: var(--white);
    text-anchor: middle;
  }
  .price-label {
    font-family: "Roboto", sans-serif;
    font-weight: 700;
    font-size: 24px;
    fill: var(--label-grey);
    text-anchor: middle;
  }
  .promo-text { font-weight: 700; font-size: 42px; fill: var(--white); }
  .extra-line { font-weight: 900; }
  .hours-heading {
    font-family: "Roboto", sans-serif;
    font-weight: 700;
    font-size: 26px;
    fill: var(--white);
    text-anchor: middle;
  }
  .hours-line { font-weight: 400; font-size: 36px; fill: var(--teal); text-anchor: middle; }
</style>
</head>
<body>
<main class="stage">
  <svg class="pylon-face" width="668" height="1200" viewBox="0 0 952 1710" xmlns="http://www.w3.org/2000/svg">
    <defs>
      <radialGradient id="rays-glow" cx="0.55" cy="0.35" r="0.8">
        <stop offset="0" stop-color="#bdeef7"/>
        <stop offset="0.5" stop-color="var(--sky)"/>
        <stop offset="1" stop-color="var(--sky-deep)"/>
      </radialGradient>
      <radialGradient id="deep-water" cx="0.5" cy="0.35" r="0.75">
        <stop offset="0" stop-color="#0bb0d6"/>
        <stop offset="0.35" stop-color="var(--ocean)"/>
        <stop offset="0.75" stop-color="var(--navy)"/>
        <stop offset="1" stop-color="var(--navy-deep)"/>
      </radialGradient>
      <linearGradient id="car-tone" x1="0" y1="0" x2="0" y2="1">
        <stop offset="0" stop-color="#3aa6e0"/>
        <stop offset="1" stop-color="#0b4f9c"/>
      </linearGradient>
      <linearGradient id="silver" x1="0" y1="0" x2="0" y2="1">
        <stop offset="0" stop-color="#ffffff"/>
        <stop offset="0.5" stop-color="#c9ced6"/>
        <stop offset="1" stop-color="#eef0f3"/>
      </linearGradient>
    </defs>

    <!-- Sky area -->
    <rect class="sky-field" x="0" y="0" width="952" height="700" fill="url(#rays-glow)" role="img" aria-label="Hellblauer Strahlenhintergrund"/>

    <!-- Deep blue body with wave edge -->
    <path class="deep-body" d="M0,443 C250,400 450,470 620,560 C720,610 850,625 952,585 L952,1710 L0,1710 Z" fill="url(#deep-water)"/>
    <path class="wave-band" d="M0,330 C250,318 450,420 600,500 C720,560 850,570 952,505 L952,590 C850,628 720,612 620,562 C450,472 250,402 0,445 Z" fill="var(--white)"/>

    <!-- Title banner -->
    <path class="title-banner" d="M94,105 L360,72 Q490,-2 620,72 L891,105 L845,258 L570,236 Q490,262 410,236 L150,276 Z" fill="var(--signal-red)" stroke="var(--banner-edge)" stroke-width="8" stroke-linejoin="round"/>
    <text class="title" x="490" y="232" font-size="150" text-anchor="middle" textLength="680" lengthAdjust="spacingAndGlyphs" fill="var(--white)" stroke="var(--navy-deep)" stroke-width="10" paint-order="stroke">AUTOWÄSCHE</text>

    <!-- Car illustration area -->
    <rect class="hero-car" x="426" y="228" width="310" height="215" rx="40" fill="url(#car-tone)" role="img" aria-label="Illustration eines glänzenden blauen Autos mit Seifenblasen"/>

    <!-- Feature list -->
    <g class="feature-ticks">
      <g transform="translate(74,600)">
        <circle r="34" fill="var(--signal-red)"/>
        <path d="M-20,2 L-6,16 L46,-26" fill="none" stroke="var(--white)" stroke-width="9" stroke-linecap="round" stroke-linejoin="round"/>
      </g>
      <g transform="translate(74,780)">
        <circle r="34" fill="var(--signal-red)"/>
        <path d="M-20,2 L-6,16 L46,-26" fill="none" stroke="var(--white)" stroke-width="9" stroke-linecap="round" stroke-linejoin="round"/>
      </g>
      <g transform="translate(74,900)">
        <circle r="34" fill="var(--signal-red)"/>
        <path d="M-20,2 L-6,16 L46,-26" fill="none" stroke="var(--white)" stroke-width="9" stroke-linecap="round" stroke-linejoin="round"/>
      </g>
      <g transform="translate(74,1023)">
        <circle r="34" fill="var(--signal-red)"/>
        <path d="M-20,2 L-6,16 L46,-26" fill="none" stroke="var(--white)" stroke-width="9" stroke-linecap="round" stroke-linejoin="round"/>
      </g>
    </g>
    <text class="bullet-text" x="141">
      <tspan x="141" y="609">Unsere verschiedenen</tspan>
      <tspan x="141" y="653">Waschprogramme</tspan>
      <tspan x="141" y="697">garantieren Ihnen echte Qualität und</tspan>
    </text>
    <text class="bullet-text" x="141">
      <tspan x="141" y="781">Alle unsere Waschprogramme</tspan>
      <tspan x="141" y="825">nutzen Aktiv-Schaum</tspan>
    </text>
    <text class="bullet-text" x="138">
      <tspan x="138" y="908">Neuwertiger Waschtechnik zu</tspan>
      <tspan x="138" y="953">glänzenden Ergebnissen</tspan>
    </text>
    <text class="bullet-text" x="132">
      <tspan x="132" y="1034">Und nutzen Sie unsere Bonuskarte.</tspan>
      <tspan x="132" y="1079">Nach 10 Wäschen erhalten</tspan>
      <tspan x="132" y="1124">1 Wäsche kostenlos  nach  Wahl</tspan>
    </text>

    <!-- Price badges -->
    <g class="price-badges">
      <circle cx="158" cy="1231" r="68" fill="var(--signal-red)"/>
      <circle cx="368" cy="1231" r="68" fill="var(--signal-red)"/>
      <circle cx="569" cy="1231" r="68" fill="var(--signal-red)"/>
      <circle cx="767" cy="1231" r="68" fill="var(--signal-red)"/>
      <text class="price-euro" font-size="50" x="152" y="1218">€</text>
      <text class="price-euro" font-size="50" x="365" y="1218">€</text>
      <text class="price-euro" font-size="50" x="567" y="1218">€</text>
      <text class="price-euro" font-size="50" x="763" y="1218">€</text>
      <text class="price-value" font-size="50" x="160" y="1276">7.50</text>
      <text class="price-value" font-size="50" x="368" y="1276">10.50</text>
      <text class="price-value" font-size="50" x="570" y="1276">13.00</text>
      <text class="price-value" font-size="50" x="767" y="1276">15.50</text>
      <text class="price-label" x="152" y="1331">GRUNDLEGENDE</text>
      <text class="price-label" x="152" y="1354">WÄSCHE</text>
      <text class="price-label" x="373" y="1331">KOMFORT</text>
      <text class="price-label" x="373" y="1352">PFLEGE</text>
      <text class="price-label" x="579" y="1330">BESONDERE</text>
      <text class="price-label" x="579" y="1350">PFLEGE</text>
      <text class="price-label" x="773" y="1331">PREMIUM</text>
      <text class="price-label" x="773" y="1351">PFLEGE</text>
    </g>

    <!-- Promo tag -->
    <polygon class="promo-tag" points="476,1376 878,1376 878,1471 441,1471" fill="var(--signal-red)"/>
    <text class="promo-text">
      <tspan x="494" y="1419">Perfekte Wäsche</tspan>
      <tspan x="494" y="1462">auch für 1hr Auto</tspan>
    </text>

    <!-- Sports car line art area -->
    <rect class="car-outline" x="61" y="1393" width="280" height="140" rx="20" fill="#2a4f8f" opacity="0.55" role="img" aria-label="Weiße Linienzeichnung eines Sportwagens mit Glanzsternen"/>

    <!-- Extra offer -->
    <text class="extra-line" x="878" y="1537" font-size="48" text-anchor="end" fill="var(--gold)">ETWAS BESONDERES</text>
    <text class="extra-line" x="61" y="1602" font-size="72" textLength="815" lengthAdjust="spacingAndGlyphs" fill="url(#silver)">ZUSÄTZLICH LOTUSWACHS</text>

    <!-- Opening hours -->
    <text class="hours-heading" x="476" y="1653">ÖFFNUNGSZEITEN</text>
    <text class="hours-line" x="476" y="1690">Mo-Frei. 08:00-19:00 Uhr,  Sa 07:00-19:00 Uhr</text>
  </svg>
</main>
</body>
</html>
```